Brightway Haul & Upkeep Services, are a company that offers a 'one stop shop' pre-move clean up a

I have already selected a logo which I would like on the front of the business cards along with phone numbers, web address and email which are:
0487650392
www.brightwayhaul.com.au
brightwayhaulandupkeep@mailbox.example

On the back of the card I would like to list some of the types of service we offer (clean - move - repairs/maintenance) which are:
CLEAN - windows, gutters, solar panels, driveways/paths, carpets.
MOVE - Small/medium size house/office moves, large item pick-up & delivery, yard clean-up and removal.
General maintenance and repairs.

I would like the blue logo on a gray background.

Thanks

```html
<!DOCTYPE html>
<html lang="en">
<head>
<meta charset="utf-8">
<title>Brightway Haul &amp; Upkeep Services – Business Cards</title>
<link rel="stylesheet" href="https://fonts.googleapis.com/css2?family=Open+Sans:wght@400;600;700;800&display=swap">
<style>
  :root {
    --brand-blue: #2f7bc4;
    --ink: #262626;
    --band-black: #1f1f1f;
    --card-top: #f4f4f4;
    --card-bottom: #c9cacc;
    --backdrop: #e6e6e6;
  }
  * { box-sizing: border-box; margin: 0; padding: 0; }
  html, body { width: 1200px; height: 790px; overflow: hidden; }
  body {
    background: var(--backdrop);
    font-family: "Open Sans", Arial, sans-serif;
    color: var(--ink);
    position: relative;
  }
  .card {
    position: absolute;
    width: 560px;
    height: 320px;
    background: linear-gradient(180deg, var(--card-top) 0%, var(--card-bottom) 100%);
    box-shadow: 0 6px 18px rgba(0,0,0,0.18);
    overflow: hidden;
  }
  .card--front { left: 40px; top: 70px; }
  .card--back  { left: 600px; top: 400px; background: linear-gradient(180deg, #f6f6f6 0%, #d8d9db 100%); }

  /* Front */
  .front-name {
    position: absolute;
    left: 26px; top: 98px;
    width: 210px;
    display: flex; align-items: flex-start; gap: 9px;
  }
  .name-mark {
    flex: none;
    width: 14px; height: 14px;
    background: var(--brand-blue);
    margin-top: 5px;
  }
  .brand-name {
    font-weight: 800;
    color: var(--brand-blue);
    text-transform: uppercase;
    line-height: 1.1;
  }
  .front-name .brand-name { font-size: 20px; }
  .divider {
    position: absolute;
    left: 250px; top: 72px;
    width: 1px; height: 110px;
    background: linear-gradient(180deg, rgba(0,0,0,0), rgba(0,0,0,0.35), rgba(0,0,0,0));
  }
  .contact-list {
    position: absolute;
    left: 264px; top: 82px;
    width: 280px;
    list-style: none;
    font-size: 11.5px;
  }
  .contact-list li {
    display: flex; align-items: center; gap: 7px;
    height: 30px;
    white-space: nowrap;
  }
  .contact-list li:first-child { font-size: 15px; }
  .contact-list svg { width: 12px; height: 12px; flex: none; }
  .front-bands { position: absolute; left: 0; bottom: 0; width: 560px; height: 90px; }

  /* Back */
  .back-name {
    position: absolute;
    left: 30px; right: 30px; top: 28px;
    text-align: center;
  }
  .back-name .brand-name { font-size: 40px; line-height: 1.05; }
  .services-heading {
    position: absolute;
    left: 0; right: 0; top: 160px;
    text-align: center;
    color: var(--brand-blue);
    font-weight: 600;
    font-size: 20px;
    letter-spacing: 7px;
  }
  .service-list {
    position: absolute;
    left: 0; right: 0; top: 200px;
    list-style: none;
    text-align: center;
    font-size: 18px;
    font-weight: 400;
    text-transform: uppercase;
    line-height: 1.6;
  }
</style>
</head>
<body>

  <section class="card card--front" aria-label="Business card front">
    <div class="front-name">
      <span class="name-mark" aria-hidden="true"></span>
      <span class="brand-name">Brightway Haul &amp; Upkeep Services</span>
    </div>
    <div class="divider"></div>
    <ul class="contact-list">
      <li>
        <svg viewBox="0 0 24 24" aria-hidden="true"><circle cx="12" cy="12" r="11" fill="none" stroke="#262626" stroke-width="2"/><path d="M8 6c1 0 2 2 2 3s-1 1-1 2 2 3 3 3 1-1 2-1 3 1 3 2-1 2-3 2c-4 0-8-5-8-8 0-2 1-3 2-3z" fill="#262626"/></svg>
        0487650392
      </li>
      <li>
        <svg viewBox="0 0 24 24" aria-hidden="true"><rect x="2" y="5" width="20" height="14" fill="#262626"/><path d="M2 5l10 8 10-8" fill="none" stroke="#f0f0f0" stroke-width="2"/></svg>
        brightwayhaulandupkeep@mailbox.example
      </li>
      <li>
        <svg viewBox="0 0 24 24" aria-hidden="true"><circle cx="12" cy="12" r="10" fill="none" stroke="#262626" stroke-width="2"/><path d="M2 12h20M12 2c4 4 4 16 0 20M12 2c-4 4-4 16 0 20" fill="none" stroke="#262626" stroke-width="1.5"/></svg>
        www.brightwayhaul.com.au
      </li>
    </ul>
    <svg class="front-bands" viewBox="0 0 560 90" preserveAspectRatio="none" aria-hidden="true">
      <polygon points="0,68 295,50 265,90 0,90" fill="var(--brand-blue)"/>
      <polygon points="305,48 560,18 560,90 275,90" fill="var(--band-black)"/>
    </svg>
  </section>

  <section class="card card--back" aria-label="Business card back">
    <div class="back-name">
      <span class="brand-name">Brightway Haul &amp; Upkeep Services</span>
    </div>
    <p class="services-heading">Services we offer</p>
    <ul class="service-list">
      <li>• Clean &nbsp;• Move</li>
      <li>• General maintenance and repairs.</li>
    </ul>
  </section>

</body>
</html>
```